Start up Dialysis Clinic needs its first website - Velmira Health

Create a visually appealing and user-friendly website for Velmira Health, a dialysis clinic located in Mt. Irvine, Tobago. The website should effectively communicate our services to local, regional, and international patients, providing essential information and fostering trust and engagement..
Key Goals:

1. Informative: Provide comprehensive information about our services, facility, and team.
2. User-Friendly: Ensure the website is easy to navigate, with a clear structure and accessible content.
3. Engaging: Create a visually appealing design that reflects the professionalism and care of Velmira Health.
4. Responsive: Ensure the website is fully responsive and performs well on all devices, including desktops, tablets, and smartphones.
5. Trust-Building: Include testimonials, credentials, and patient resources to build trust with potential patients.
Scope of Work:

1. Home Page: An inviting and informative landing page that provides an overview of our clinic, mission, and services. Include a call to action for more information and contact details.
2. About Us: A detailed page about Velmira Health, including our mission, vision, team, and facility tour.
3. Services: A comprehensive page describing the dialysis services we offer, including Hemodialysis, Peritoneal Dialysis, and Home Hemodialysis.
4. Patient Information: A resourceful section with guides for new patients, FAQs, insurance and billing information, and downloadable forms.
5. Resources: Educational content about kidney health, dialysis options, diet and nutrition tips, and support groups.
6. Contact Us: A contact page with our address, phone number, email, office hours, a contact form, and a map.

```html
<!DOCTYPE html>
<html lang="en">
<head>
<meta charset="utf-8">
<title>Velmira Health — Dialysis Clinic, Mt. Irvine</title>
<link href="https://fonts.googleapis.com/css2?family=Open+Sans:wght@400;600;700;800&display=swap" rel="stylesheet">
<style>
:root{
  --navy:#0f2a4a;
  --navy-deep:#14304f;
  --blue:#3d74b9;
  --green:#4e8a2c;
  --green-bright:#5c9c33;
  --ice:#eef6fb;
  --text:#222a33;
  --muted:#6c7480;
  --line:#d8dde3;
  --white:#ffffff;
  --footer:#173a55;
  --orange:#e98a1c;
}
*{box-sizing:border-box;margin:0;padding:0}
html,body{width:1200px;height:4320px;overflow:hidden}
body{font-family:"Open Sans",Arial,sans-serif;color:var(--text);background:var(--white);position:relative}
.abs{position:absolute}
section,header,footer{position:absolute;left:0;width:1200px;overflow:hidden}

/* header */
.site-header{top:0;height:80px;background:var(--white);box-shadow:0 2px 6px rgba(0,0,0,.08);z-index:5}
.topbar{position:absolute;left:395px;top:0;width:805px;height:37px}
.topbar-info{position:absolute;top:10px;font-size:9px;color:#fff}
.quote-btn{position:absolute;left:845px;top:14px;width:110px;height:12px;background:#3a6d8a;color:#fff;font-size:9px;text-align:center;line-height:12px}
.brand{position:absolute;left:125px;top:20px;display:flex;flex-direction:column;align-items:center;gap:4px}
.brand-mark{width:26px;height:26px;background:var(--blue)}
.brand-name{font-size:13px;font-weight:700;color:var(--blue);letter-spacing:.5px}
.main-nav{position:absolute;top:50px;left:403px;display:flex;gap:0;font-size:11px;color:#333}
.main-nav a{color:inherit;text-decoration:none;position:absolute;white-space:nowrap}
.main-nav a.active{color:var(--blue);font-weight:700}

/* hero */
.hero{top:80px;height:760px;background:var(--ice)}
.hero-photo{position:absolute;inset:0;background:linear-gradient(90deg,#1a3a74 0%,#2d4f80 35%,#7f8ea3 55%,#a9b3bf 75%,#8aa6c6 100%)}
.hero-title{position:absolute;left:128px;top:182px;font-size:40px;line-height:49px;font-weight:700;color:#fff}
.hero-text{position:absolute;left:129px;top:306px;width:450px;font-size:19px;line-height:28px;color:#fff}
.btn-pill{position:absolute;left:129px;top:420px;width:155px;height:42px;border-radius:21px;background:var(--green);color:#fff;font-size:12px;font-weight:700;text-align:center;line-height:42px}

/* about */
.who{top:840px;height:562px;background:var(--ice)}
.eyebrow{font-size:12px;color:var(--green);text-decoration:underline;text-underline-offset:4px;font-weight:600}
.center{text-align:center;left:0;width:1200px}
.h-big{font-size:42px;font-weight:700;color:var(--navy)}
.h-big span,.accent{color:var(--blue)}
.who-text{left:175px;width:850px;font-size:14px;line-height:22px;color:var(--muted);text-align:center}
.feature-card{position:absolute;top:243px;width:276px;height:242px;background:var(--white);border-bottom:4px solid var(--green);box-shadow:0 2px 10px rgba(0,0,0,.06);text-align:center}
.feature-card h3{position:absolute;left:0;width:100%;font-size:21px;font-weight:700;color:#4e5561;letter-spacing:.5px}
.feature-card p{position:absolute;left:35px;width:206px;top:85px;font-size:13px;line-height:21px;color:var(--muted)}
.feature-card svg{position:absolute;left:108px;top:55px}

/* partner */
.partner{top:1402px;height:658px;background:var(--white)}
.partner h2{position:absolute;left:133px;top:160px;font-size:36px;line-height:46px;font-weight:700;color:var(--navy)}
.partner h4{position:absolute;left:133px;top:278px;font-size:20px;font-weight:600;color:#111}
.partner .copy{position:absolute;left:133px;width:460px;font-size:12px;line-height:19px;color:var(--muted)}
.btn-square{position:absolute;left:133px;top:450px;width:137px;height:40px;background:var(--green);color:#fff;font-size:14px;font-weight:700;line-height:40px;padding-left:14px}

/* services */
.services{top:2060px;height:450px;background:var(--navy)}
.service-panel{position:absolute;top:0;width:400px;height:450px}
.service-band{position:absolute;top:0;width:60px;height:450px;background:#1d2f5a}
.band-text{position:absolute;left:10px;bottom:55px;width:260px;transform:rotate(-90deg);transform-origin:0 100%;color:#fff;font-size:11px;line-height:14px;white-space:nowrap}
.band-text b{display:block;font-size:14px}
.service-feature{position:absolute;left:440px;top:325px;width:330px;color:#fff}
.service-feature h3{font-size:15px;font-weight:700}
.service-feature p{font-size:12.5px;line-height:20px}

/* testimonials */
.testimonials{top:2510px;height:643px;background:var(--ice)}
.testimonials .label{top:66px;font-size:16px;color:var(--green);font-weight:600}
.testimonials h2{top:96px;font-size:32px;font-weight:700;color:var(--navy)}
.quote-text{left:300px;width:600px;top:390px;font-size:18px;line-height:31px;text-align:center;color:#222}
.stars{left:0;width:1200px;top:498px;text-align:center;color:var(--orange);font-size:18px;letter-spacing:2px}
.client-name{top:522px;font-size:17px;font-weight:700;color:var(--orange)}
.client-role{top:553px;font-size:10px;color:#333}

/* contact */
.contact{top:3153px;height:720px;background:var(--white)}
.contact h2{position:absolute;left:140px;top:130px;font-size:34px;line-height:43px;font-weight:600;color:#111}
.contact h2 span{font-weight:400;color:var(--blue)}
.contact .copy{position:absolute;left:140px;top:214px;width:380px;font-size:13px;line-height:21px;color:var(--muted)}
.contact-rule{position:absolute;left:140px;top:330px;width:378px;height:1px;background:var(--line)}
.contact-item{position:absolute;left:140px;display:flex;align-items:center;gap:22px;font-size:13px;color:var(--muted)}
.icon-dot{width:35px;height:35px;border-radius:50%;background:#fff;box-shadow:0 2px 8px rgba(0,0,0,.12);display:flex;align-items:center;justify-content:center}
.form-card{position:absolute;left:588px;top:62px;width:487px;height:545px;background:#fff;border-top:3px solid var(--green);border-radius:6px;box-shadow:0 2px 14px rgba(0,0,0,.1)}
.form-label{position:absolute;font-size:13px;font-weight:700;color:var(--blue)}
.form-field{position:absolute;height:45px;border:1px solid #c9ced4;border-radius:2px;font-size:11px;color:#999;padding:13px 16px}
.btn-submit{position:absolute;left:31px;top:452px;width:127px;height:42px;background:var(--green);color:#fff;font-size:14px;font-weight:700;text-align:center;line-height:42px}

/* footer */
.site-footer{top:3810px;height:510px}
.footer-title{position:absolute;top:258px;font-size:15px;font-weight:700;color:#fff}
.footer-line{position:absolute;font-size:11.5px;line-height:20px;color:#fff}
.social{position:absolute;top:382px;left:535px;display:flex;gap:8px}
.social span{width:36px;height:36px;border:1px solid #fff;display:block}
.footer-rule{position:absolute;left:62px;top:448px;width:1076px;height:1px;background:rgba(255,255,255,.35)}
.copyright{position:absolute;top:468px;left:0;width:1200px;text-align:center;font-size:12px;color:#d6dfe6}
</style>
</head>
<body>

<header class="site-header">
  <svg class="abs" style="left:390px;top:0" width="810" height="37" viewBox="0 0 810 37" aria-hidden="true">
    <path d="M0 0 H810 V37 H75 C45 37 40 0 0 0 Z" fill="#0f2a4a"/>
  </svg>
  <div class="topbar">
    <div class="topbar-info" style="left:72px">● 48 Harbour Rd., Mt. Irvine, Tobago</div>
    <div class="topbar-info" style="left:310px">Follow Us: <span style="letter-spacing:6px">■■■</span></div>
  </div>
  <div class="quote-btn">GET QUOTATION</div>
  <div class="brand"><span class="brand-mark"></span><span class="brand-name">Velmira Health</span></div>
  <nav class="main-nav">
    <a class="active" style="left:0">Home</a>
    <a style="left:82px">Services</a>
    <a style="left:162px">About Us</a>
    <a style="left:238px">Our Team</a>
    <a style="left:313px">And more</a>
    <a style="left:388px">Contact Us</a>
  </nav>
</header>

<section class="hero">
  <div class="hero-photo" role="img" aria-label="Doctor and nurse in masks reviewing a clipboard in a hospital corridor"></div>
  <svg class="abs" style="left:0;top:540px" width="1200" height="220" viewBox="0 0 1200 220" aria-hidden="true">
    <path d="M0 245 V160 C300 175 700 120 1200 85 V245 Z" fill="#3f6f9c"/>
    <path d="M0 220 V195 C350 180 700 130 1200 85 V220 Z" fill="#eef6fb"/>
    <path d="M0 160 C350 160 750 115 820 150 L0 195 Z" fill="#eef6fb" opacity="0"/>
    <path d="M120 175 C420 165 700 140 820 125" stroke="#4e8a2c" stroke-width="5" fill="none"/>
    <path d="M0 160 C300 160 700 110 1200 85 V0 H1200 V85" fill="none"/>
  </svg>
  <h1 class="hero-title">Empower your Body,<br>Empower your Life.</h1>
  <p class="hero-text">Lorem ipsum dolor sit amet, consectetur adipi scing elit, sed do eiusmod tempor incidid unt ut labore et dolore magna aliqua.</p>
  <div class="btn-pill">READ MORE</div>
</section>

<section class="who">
  <div class="abs center" style="top:30px"><span class="eyebrow">WHO WE ARE</span></div>
  <h2 class="abs center h-big" style="top:65px">Recharge your <span>health</span></h2>
  <p class="abs who-text" style="top:135px">Lorem ipsum dolor sit amet, consectetur adipiscing elit, sed do eiusmod tempor incididunt ut labore et dolore magna aliqua. Ut enim ad minim veniam, quis laboris nisi ut aliquip ex ea commodo consequat. Lorem ipsum dolor sit am et, consectetur adipiscing elit, sed do eiusmod te</p>
  <div class="feature-card" style="left:152px">
    <svg width="60" height="60" viewBox="0 0 60 60" fill="none" stroke="#4e8a2c" stroke-width="3"><path d="M14 50 H50 M20 50 C20 38 30 32 40 36 M26 8 L34 14 L24 34 L16 28 Z M24 34 L28 40"/></svg>
    <h3 style="top:152px">CLIENT-CENTRIC</h3>
  </div>
  <div class="feature-card" style="left:462px">
    <h3 style="top:37px">PROFESSIONAL</h3>
    <p>Lorem ipsum dolor sit amet, consectetur adipiscing elit, sed do eiusmod tempor incidid unt ut labore et dolore magna ali</p>
  </div>
  <div class="feature-card" style="left:768px">
    <svg width="64" height="64" viewBox="0 0 64 64" fill="none" stroke="#4e8a2c" stroke-width="3"><path d="M32 8 L54 24 L46 52 H18 L10 24 Z"/><circle cx="32" cy="8" r="5" fill="#fff"/><circle cx="54" cy="24" r="5" fill="#fff"/><circle cx="46" cy="52" r="5" fill="#fff"/><circle cx="18" cy="52" r="5" fill="#fff"/><circle cx="10" cy="24" r="5" fill="#fff"/></svg>
    <h3 style="top:152px">EXPERTISE</h3>
  </div>
</section>

<section class="partner">
  <div class="abs" style="left:133px;top:128px"><span class="eyebrow" style="font-size:11px">WHO WE ARE</span></div>
  <h2>Your Partner in <span class="accent">Kidney<br>Wellness.</span></h2>
  <h4>Transform your body, transform your life.</h4>
  <p class="copy" style="top:325px">Lorem ipsum dolor sit amet, consectetur adipiscing elit, sed do eiusmod temp or incididunt ut labore et dolore magna aliqua. Ut enim ad minim veniam, quis laboris nisi ut aliquip ex ea commodo consequat.</p>
  <p class="copy" style="top:385px">Lorem ipsum dolor sit amet, consectetur adipiscing elit, sed do eiusmod temp or incididunt ut labore et dolore magna aliqua.</p>
  <div class="btn-square">Contact us &nbsp;→</div>
  <svg class="abs" style="left:630px;top:85px" width="540" height="480" viewBox="0 0 540 480">
    <circle cx="295" cy="200" r="210" fill="#eef0dd"/>
    <circle cx="280" cy="222" r="212" fill="#9fb4c9" role="img" aria-label="Doctor writing notes on a clipboard at a desk"/>
    <circle cx="430" cy="130" r="88" fill="#c9d5de" role="img" aria-label="Smiling doctor holding a clipboard"/>
    <circle cx="65" cy="420" r="45" fill="#4e8a2c"/>
  </svg>
</section>

<section class="services">
  <div class="service-panel" style="left:0;background:linear-gradient(135deg,#c8b7a8,#9c5a5a 60%,#6f8fb0)" role="img" aria-label="Patient's hand with a hemodialysis line"></div>
  <div class="service-band" style="left:340px"></div>
  <div class="band-text" style="left:362px"><b>→ Hemodialysis</b>Lorem ipsum dolor sit amet, consectetu</div>
  <div class="service-panel" style="left:400px;background:linear-gradient(160deg,#4a5567,#1f2b45)" role="img" aria-label="Doctor examining a kidney model through a magnifying glass"></div>
  <div class="abs" style="left:438px;top:248px;width:58px;height:58px;border-radius:50%;background:#fff"></div>
  <div class="service-feature">
    <h3>Peritoneal Dialysis</h3>
    <p>Lorem ipsum dolor sit amet, consectetur adipiscing elit, sed do eiusmod tempor incididunt ut labore et dolore magna aliqua. Ut enim ad minim</p>
    <p style="font-size:18px">⟶</p>
  </div>
  <div class="service-panel" style="left:800px;background:linear-gradient(135deg,#2e4a78,#6e87a8 50%,#c9a48f)" role="img" aria-label="Arm connected to dialysis tubing"></div>
  <div class="service-band" style="left:1140px"></div>
  <div class="band-text" style="left:1162px"><b>→ Home Hemodialysis</b>Lorem ipsum dolor sit amet, consectetu</div>
</section>

<section class="testimonials">
  <div class="abs center label">TESTIMONIALS</div>
  <h2 class="abs center">What Our <span class="accent">Clients</span> are Saying</h2>
  <svg class="abs" style="left:0;top:0" width="1200" height="643" viewBox="0 0 1200 643">
    <path d="M198 378 Q600 40 1010 378" fill="none" stroke="#3d74b9" stroke-width="2" stroke-dasharray="6 5"/>
    <circle cx="198" cy="378" r="38" fill="#b9a89b" role="img" aria-label="Client portrait"/>
    <circle cx="383" cy="255" r="36" fill="#a79386" role="img" aria-label="Client portrait"/>
    <circle cx="604" cy="200" r="60" fill="#8c7b6e" role="img" aria-label="Client portrait"/>
    <circle cx="825" cy="255" r="36" fill="#b5a293" role="img" aria-label="Client portrait"/>
    <circle cx="1010" cy="378" r="38" fill="#a9a39d" role="img" aria-label="Client portrait"/>
    <text x="602" y="372" text-anchor="middle" font-family="Open Sans, sans-serif" font-size="70" font-weight="800" fill="#4e8a2c">“</text>
    <circle cx="488" cy="533" r="22" fill="#14304f"/>
    <path d="M498 533 H478 M486 525 L478 533 L486 541" stroke="#fff" stroke-width="2" fill="none"/>
    <circle cx="718" cy="533" r="22" fill="#5c9c33"/>
    <path d="M708 533 H728 M720 525 L728 533 L720 541" stroke="#fff" stroke-width="2" fill="none"/>
  </svg>
  <p class="abs quote-text">Lorem ipsum dolor sit amet, consectetur adipiscing elit, sed do eiusmod te dunt ut labore et dolore magna aliqua .dipiscing elit, sed do eiusmod temp dunt ut labore et dolore magna aliqua .dipiscing elit, sed</p>
  <div class="abs stars">★★★★★</div>
  <div class="abs center client-name">Daniel Moreau</div>
  <div class="abs center client-role">Client</div>
</section>

<section class="contact">
  <h2>Get &nbsp;in Touch<br><span>Contact Us</span></h2>
  <p class="copy">Lorem ipsum dolor sit amet, consectetur adipiscing e lit, sed do eiusmod tempor incididunt ut labore et dolore magna aliqua. ceptos ...</p>
  <div class="contact-rule"></div>
  <div class="contact-item" style="top:357px"><span class="icon-dot"><svg width="14" height="16" viewBox="0 0 14 16"><path d="M7 0C3 0 1 3 1 6c0 4 6 10 6 10s6-6 6-10c0-3-2-6-6-6z" fill="#3d74b9"/><circle cx="7" cy="6" r="2" fill="#fff"/></svg></span>Shore Lane 7, Mt. Irvine</div>
  <div class="contact-item" style="top:420px"><span class="icon-dot"><svg width="14" height="14" viewBox="0 0 14 14"><path d="M3 1 L5 4 L4 6 C5 8 6 9 8 10 L10 9 L13 11 L11 13 C6 13 1 8 1 3 Z" fill="#3d74b9"/></svg></span>+1 868 555 0142</div>
  <div class="contact-item" style="top:475px"><span class="icon-dot"><svg width="14" height="10" viewBox="0 0 14 10"><rect width="14" height="10" rx="1" fill="#14304f"/><path d="M1 1 L7 6 L13 1" stroke="#fff" fill="none"/></svg></span>office@velmira.example</div>
  <div class="form-card">
    <div class="form-label" style="left:36px;top:52px">Full Name:</div>
    <div class="form-field" style="left:31px;top:80px;width:424px">Sed non neque elit.</div>
    <div class="form-label" style="left:36px;top:155px">Email :</div>
    <div class="form-field" style="left:31px;top:184px;width:197px">Sed non neque elit.</div>
    <div class="form-label" style="left:262px;top:155px">Phone no :</div>
    <div class="form-field" style="left:258px;top:184px;width:197px">Sed non neque elit.</div>
    <div class="form-label" style="left:36px;top:265px">Messages &nbsp;:</div>
    <div class="form-field" style="left:31px;top:293px;width:424px;height:130px">Sed non neque elit.</div>
    <div class="btn-submit">SUBMIT</div>
  </div>
</section>

<footer class="site-footer">
  <svg class="abs" style="left:0;top:0" width="1200" height="510" viewBox="0 0 1200 510" aria-hidden="true">
    <path d="M390 90 C600 40 900 25 1200 0 V60 C900 75 600 80 390 90 Z" fill="#4e8a2c"/>
    <path d="M0 200 C150 120 350 80 600 65 C850 50 1000 45 1200 50 V510 H0 Z" fill="#173a55"/>
  </svg>
  <div class="abs" style="left:548px;top:162px;width:80px;height:80px;border:3px solid #fff"></div>
  <div class="abs center" style="top:250px;font-size:30px;font-weight:700;color:#fff;letter-spacing:1px">Velmira Health</div>
  <p class="footer-line" style="left:455px;width:290px;top:300px;text-align:center">Lorem ipsum dolor sit amet, consectetur adipisc ing elit, sed do eiusmod tempor incididunt labore et dolore magna</p>
  <div class="social"><span></span><span></span><span></span></div>
  <div class="footer-title" style="left:93px">CONTACT US</div>
  <div class="footer-line" style="left:93px;top:292px">● &nbsp;&nbsp;101- lorem ipsum simple text<br>&nbsp;&nbsp;&nbsp;&nbsp;&nbsp;print type text industry text.</div>
  <div class="footer-line" style="left:93px;top:345px">✆ &nbsp;&nbsp;868 555 0190</div>
  <div class="footer-line" style="left:93px;top:382px">✉ &nbsp;&nbsp;info@velmira.example</div>
  <div class="footer-title" style="left:971px">OPENING HOURS</div>
  <div class="footer-line" style="right:90px;top:298px;text-align:right">Mon - Fri: 9am - to - 6pm &nbsp;&nbsp;◷</div>
  <div class="footer-line" style="right:90px;top:329px;text-align:right">Saturday 9am - to - 2pm &nbsp;&nbsp;◷</div>
  <div class="footer-line" style="right:90px;top:360px;text-align:right">Sunday : <u>Closed</u> &nbsp;&nbsp;◷</div>
  <div class="footer-rule"></div>
  <div class="copyright">Velmira Health</div>
</footer>

</body>
</html>
```